Hardcore nerd needs to stand out in a sea of dull Defence business cards

Wombarra Devices is a new Australian consulting engineering company that turns research and theory into practical systems. No evangelistic fluff, just mathematics and physics into electronic and optical circuits for consumer products, scientific research or Defence applications.

We already have a recognised logo (provided) which is often dark blue/black on a light background but we're open to other combinations. (Us engineers tend to have limited aesthetic imagination :)

Some of our recent products have included:
* Instrumentation for electrical testing,
* Radar jammers,
* GPS antenna design,
* Satellite tracking systems,
* High power lasers

We're open to both single and double-sided designs - happy to be convinced either way.

P.S. Another group is working on the web page, so - alas - our web site is currently of no use for images/ideas...

Target Market(s)

Engineering managers,
Scientists

Contact Information for Business Card

Dr Colin Harte
R&D Engineer

colin@wombarradevices.com.au
0427 563 710

PO Box XXX (to be confirmed)
Kelsby ACT 2917
Australia

Font styles to use
Serif
Sans Serif

Colors

Designer to choose colors to be used in the design.

Requirements
Must have
• My contact details!
• I've had many (great) "bold and plain" designs submitted already, so feel free to be artistically creative :)
• Happy to take advice re fonts/colours/printability etc.
Nice to have
• I'm not sure if "lists" are more at home on a CV than a business card, but representative services include:
• Applied electromagnetics
• RF and high speed electronics
• Signal and image processing
• Electro-optical and laser systems
• Concept-to-prototype design services
• If you're considering double sided cards, then often measuring/alignment grids/rulers feature on the back of similar cards.
• e.g. https://www.veltranoptics.example/newgrouppage9.cfm?objectgroup_id=4183
• https://www.veltranoptics.example/newgrouppage9.cfm?objectgroup_ID=4185
• ..or even a "Smith chart" (google will return lots)
• Generic images to represent a capability might work - googling images associated with keyword for each of these areas might help:
• - "passive radar", "phased array", "fdtd", "vircator"
• RF and high speed electronic design
• - "smith chart", "microstrip circuits", "dimensioned drawing", "electronic schematic"
• - "dft", "iir filter"
• - "optical cavity". "laser energy level diagram"
• Background/watermarked images outlines/wireframes/schematics would probably look OK.
Should not have
• If a list of projects/services is provided, it is important not to make the client feel that this is "all" the company can do. Engineering design is a creative discipline (like graphics :)
• Please, no stock "military" snaps like planes, missiles, etc!

```html
<!DOCTYPE html>
<html lang="en">
<head>
<meta charset="utf-8">
<title>Wombarra Devices – Business Card</title>
<link rel="stylesheet" href="https://fonts.googleapis.com/css2?family=Arimo:wght@400;700&display=swap">
<style>
  :root {
    --navy: #1f2a6b;
    --navy-deep: #18215a;
    --navy-glow: #2a3785;
    --ink-grey: #7a7a7f;
    --rule: #8a8fb3;
    --paper: #ffffff;
    --backdrop: #e6e7ec;
    --on-navy: #ffffff;
  }
  * { box-sizing: border-box; margin: 0; padding: 0; }
  html, body { width: 1200px; height: 900px; overflow: hidden; }
  body {
    background: var(--backdrop);
    font-family: "Arimo", Arial, sans-serif;
    display: flex;
    flex-direction: column;
    align-items: center;
    justify-content: center;
    gap: 44px;
  }
  .card {
    width: 630px;
    height: 360px;
    border-radius: 4px;
    box-shadow: 0 6px 18px rgba(20, 24, 60, 0.18);
    position: relative;
    overflow: hidden;
  }

  /* Front */
  .card-front {
    background: var(--paper);
    display: flex;
    align-items: center;
  }
  .front-brand {
    width: 260px;
    display: flex;
    flex-direction: column;
    align-items: center;
    gap: 14px;
  }
  .brand-dot {
    width: 74px;
    height: 74px;
    border-radius: 50%;
    background: var(--navy);
  }
  .brand-name {
    font-weight: 700;
    color: var(--navy);
    font-size: 22px;
    text-transform: uppercase;
    letter-spacing: 0.5px;
    text-align: center;
    line-height: 1.15;
  }
  .front-rule {
    width: 1px;
    align-self: stretch;
    margin: 0;
    background: var(--rule);
  }
  .contact {
    padding-left: 30px;
    color: var(--ink-grey);
    font-size: 17px;
    line-height: 1.2;
  }
  .contact-name {
    color: var(--navy);
    font-weight: 700;
    font-size: 22px;
    text-transform: uppercase;
  }
  .contact-role { margin-bottom: 2px; }
  .contact-line {
    display: flex;
    align-items: center;
    gap: 8px;
  }
  .contact-line svg { width: 16px; height: 16px; flex: none; }

  /* Back */
  .card-back {
    background: radial-gradient(circle at 58% 40%, var(--navy-glow) 0, var(--navy) 42%, var(--navy-deep) 100%);
    color: var(--on-navy);
    display: flex;
    flex-direction: column;
    align-items: center;
    justify-content: center;
  }
  .back-brand {
    display: flex;
    flex-direction: column;
    align-items: center;
    gap: 12px;
    margin-top: -20px;
  }
  .back-brand .brand-dot {
    width: 56px;
    height: 56px;
    background: var(--on-navy);
  }
  .back-brand .brand-name { color: var(--on-navy); font-size: 24px; }
  .services {
    list-style: none;
    position: absolute;
    bottom: 40px;
    left: 0;
    right: 0;
    text-align: center;
    font-size: 15px;
    line-height: 1.35;
  }
  .services li { display: inline; }
  .services li::before { content: "\25AA"; margin: 0 4px 0 8px; }
</style>
</head>
<body>

  <section class="card card-front">
    <div class="front-brand">
      <div class="brand-dot"></div>
      <div class="brand-name">Wombarra<br>Devices</div>
    </div>
    <div class="front-rule"></div>
    <div class="contact">
      <p class="contact-name">Dr Colin Harte</p>
      <p class="contact-role">R&amp;D Engineer</p>
      <p>PO Box XXX</p>
      <p>Kelsby ACT 2917, Australia</p>
      <p class="contact-line">
        <svg viewBox="0 0 16 16" aria-hidden="true"><circle cx="8" cy="8" r="7" fill="none" stroke="var(--navy)" stroke-width="1.5"/><path d="M5.5 4.5l1.5 1.5-1 1c.6 1.2 1.6 2.2 2.8 2.8l1-1 1.5 1.5-1.2 1.2C7.5 11 5 8.5 4.3 5.7z" fill="var(--navy)"/></svg>
        0427 563 710
      </p>
      <p class="contact-line">
        <svg viewBox="0 0 16 16" aria-hidden="true"><rect x="1.5" y="3.5" width="13" height="9" fill="none" stroke="var(--navy)" stroke-width="1.4"/><path d="M1.5 3.5L8 9l6.5-5.5" fill="none" stroke="var(--navy)" stroke-width="1.4"/></svg>
        colin@wombarradevices.com.au
      </p>
      <p class="contact-line">
        <svg viewBox="0 0 16 16" aria-hidden="true"><circle cx="8" cy="8" r="7" fill="var(--navy)"/><path d="M1 8h14M8 1c-3 3.5-3 10.5 0 14M8 1c3 3.5 3 10.5 0 14" fill="none" stroke="#fff" stroke-width="1"/></svg>
        www.wombarradevices.com.au
      </p>
    </div>
  </section>

  <section class="card card-back">
    <div class="back-brand">
      <div class="brand-dot"></div>
      <div class="brand-name">Wombarra Devices</div>
    </div>
    <ul class="services">
      <li>Applied electromagnetics</li>
      <li>RF and high speed electronics</li>
      <li>Signal and image processing</li><br>
      <li>Electro-optical and laser systems</li>
      <li>Concept-to-prototype design services</li>
    </ul>
  </section>

</body>
</html>
```